New Business Card Design Project

Use the flyer uploaded and website www.brightoakbuilders.com for inspiration.
List Our Services on Backside of business cards
Marcus Delling
Harborline Builders Inc.
Licensed General Contractors
858-471-6093

Contact Information for Business Card

Use the flyer uploaded and website www.brightoakbuilders.com for inspiration. List Our Services on Backside of business cards Marcus Delling Harborline Builders Inc. Licensed General Contractors 858-471-6093

```html
<!DOCTYPE html>
<html lang="en">
<head>
<meta charset="utf-8">
<title>Harborline Builders – Business Card</title>
<link href="https://fonts.googleapis.com/css2?family=Montserrat:wght@300;400;500;600;700&display=swap" rel="stylesheet">
<style>
:root{
  --backdrop:#e7e3dc;
  --card-front:#ffffff;
  --card-back:#1f1f1f;
  --card-back-edge:#2a2a2a;
  --ink:#111111;
  --ink-soft:#222222;
  --light:#f2f2f2;
  --light-soft:#dcdcdc;
  --deco-hi:rgba(190,190,190,.42);
  --deco-mid:rgba(120,120,120,.22);
  --shadow:rgba(0,0,0,.35);
}
*{margin:0;padding:0;box-sizing:border-box}
html,body{width:900px;height:1200px;overflow:hidden}
body{background:var(--backdrop);font-family:"Montserrat",Arial,sans-serif;position:relative}
.card{position:absolute;border-radius:22px;box-shadow:0 8px 22px var(--shadow)}
.card-front{left:80px;top:131px;width:742px;height:440px;background:var(--card-front);color:var(--ink)}
.card-back{left:78px;top:639px;width:744px;height:439px;background:linear-gradient(135deg,var(--card-back-edge),var(--card-back));color:var(--light);overflow:hidden}

.holder{position:absolute;left:37px;top:40px}
.holder-name{font-size:26px;font-weight:700;line-height:1.1}
.holder-title{font-size:15.5px;font-weight:400;color:var(--ink-soft);margin-top:3px}

.brand-front{position:absolute;left:360px;top:100px;width:360px;display:flex;flex-direction:column;align-items:center}
.brand-front-square{width:120px;height:120px;background:var(--ink);border-radius:4px}
.brand-front-name{margin-top:30px;font-size:30px;font-weight:600;letter-spacing:.3px;color:var(--ink);white-space:nowrap}

.contact-list{position:absolute;left:35px;top:284px;list-style:none}
.contact-list li{display:flex;align-items:center;height:29px;font-size:15.5px}
.contact-list svg{width:17px;height:17px;margin-right:13px;fill:var(--ink)}
.license{position:absolute;left:35px;top:394px;font-size:15px}

.back-mark{position:absolute;left:0;top:0;width:300px;height:439px;
  background:
    radial-gradient(ellipse 150px 110px at 55% 24%,var(--deco-hi),rgba(255,255,255,0) 100%),
    linear-gradient(180deg,var(--deco-mid) 0%,rgba(0,0,0,.25) 100%)}
.brand-back{position:absolute;left:300px;top:60px;width:410px;text-align:center;font-size:29px;font-weight:300;letter-spacing:1px;color:var(--light);white-space:nowrap}
.services-heading{position:absolute;left:323px;top:145px;font-size:20px;font-weight:700;padding-bottom:4px;border-bottom:1px solid var(--light-soft)}
.services-list{position:absolute;left:327px;top:184px;list-style:none}
.services-list li{font-size:15.5px;line-height:23.6px;color:var(--light-soft);display:flex;align-items:center}
.services-list li::before{content:"";width:5px;height:5px;border-radius:50%;background:var(--light);margin-right:11px}
</style>
</head>
<body>
<section class="card card-front">
  <div class="holder">
    <div class="holder-name">Marcus Delling</div>
    <div class="holder-title">Managing Director</div>
  </div>
  <div class="brand-front">
    <div class="brand-front-square"></div>
    <div class="brand-front-name">Harborline Builders</div>
  </div>
  <ul class="contact-list">
    <li><svg viewBox="0 0 24 24"><path d="M6.6 10.8a15 15 0 0 0 6.6 6.6l2.2-2.2c.3-.3.7-.4 1-.2 1.1.4 2.3.6 3.6.6.6 0 1 .4 1 1V20c0 .6-.4 1-1 1A17 17 0 0 1 3 4c0-.6.4-1 1-1h3.5c.6 0 1 .4 1 1 0 1.3.2 2.5.6 3.6.1.3 0 .7-.2 1z"/></svg>858-471-6093</li>
    <li><svg viewBox="0 0 24 24"><path d="M2 5h20v14H2z"/><path d="M3 6l9 6.3L21 6" stroke="#fff" stroke-width="1.6" fill="none"/></svg>info@brightoakbuilders.com</li>
    <li><svg viewBox="0 0 24 24"><circle cx="12" cy="12" r="10"/><path d="M2 12h20M12 2c3 3 3 17 0 20M12 2c-3 3-3 17 0 20" stroke="#fff" stroke-width="1.3" fill="none"/></svg>www.brightoakbuilders.com</li>
  </ul>
  <div class="license">CSLB Licensed No. #1048265</div>
</section>

<section class="card card-back">
  <div class="back-mark" role="img" aria-label="Large faint grey brand decoration"></div>
  <div class="brand-back">HARBORLINE BUILDERS</div>
  <h2 class="services-heading">Our Services</h2>
  <ul class="services-list">
    <li>Remodel: Kitchen &amp; Bath</li>
    <li>Painting: Interior &amp; Exterior</li>
    <li>Flooring: Carpet, Vinyl, Wood</li>
    <li>Window: Door Replacement</li>
    <li>Plumbing: Repair &amp; Upgrades</li>
    <li>Energy Efficient Upgrades</li>
    <li>Deck &amp; Patio construction</li>
    <li>Water &amp; Mold Damage</li>
    <li>Garage Renovation</li>
  </ul>
</section>
</body>
</html>
```